Need a developer to develop and design my virtual employee recruitment solution website.

I need the entire website developed, from the design, the navigation, the contents of the website, etc. I need a professional looking website yet have that modern look. You can suggest the best fonts, color combinations to use. I need the site to be SEO friendly. I also want high quality stock photos to be used on the website. I wanted to achieve a similar website like this https://remotehelperpool.example/.

Target Market(s)

Ecommerce Entrepreneurs, Businessmen, Cartwell and Bazorra Sellers.

Industry/Entity Type

Professional Service

Coding

Coded - Design and coding required

Number of Pages Required

5+ page

Font styles to use
Sans Serif

Requirements
Must have
• I wanted it to have pages like this https://remotehelperpool.example/
Nice to have
• open for any recommendation you can suggest
Should not have
• Cannot think of any. You can suggest your own here

```html
<!DOCTYPE html>
<html lang="en">
<head>
<meta charset="utf-8">
<title>RemoteHaven – Virtual Employee Recruitment</title>
<link rel="stylesheet" href="https://fonts.googleapis.com/css2?family=Lato:wght@400;700;900&display=swap">
<style>
:root{
  --blue:#1559c4;
  --blue-bright:#1a66d6;
  --teal-text:#1d72c0;
  --dark:#2b2b2b;
  --footer:#2a2a2a;
  --gray-band:#efefef;
  --card:#eeeeee;
  --text:#333333;
  --white:#ffffff;
}
*{margin:0;padding:0;box-sizing:border-box}
html,body{width:1200px;height:2859px;overflow:hidden}
body{font-family:'Lato',sans-serif;color:var(--text);background:var(--white);position:relative}
.abs{position:absolute}
/* nav */
.topnav{left:0;top:0;width:1200px;height:60px;background:var(--dark)}
.topnav a{position:absolute;top:0;height:60px;line-height:60px;color:var(--white);font-weight:700;font-size:17px;text-decoration:none;text-transform:uppercase}
.topnav a.active{background:var(--blue-bright);padding:0 15px}
/* header */
.phone{left:75px;top:88px;display:flex;align-items:center;gap:4px;font-weight:700;font-size:23px;color:#222}
.brand{left:450px;top:96px;width:300px;text-align:center;font-weight:900;font-size:30px;color:var(--blue)}
.btn{background:var(--blue-bright);color:var(--white);font-weight:700;font-size:15px;text-transform:uppercase;display:flex;align-items:center;justify-content:center;text-decoration:none}
.hero{left:0;top:172px;width:1200px;height:555px;background:radial-gradient(ellipse at 75% 40%,#3aa2aa 0%,#1f7f8c 40%,#125566 100%)}
.hero h1{position:absolute;left:76px;top:160px;color:var(--white);font-weight:700;line-height:1}
.hero h1 .small{display:block;font-size:44px;margin-bottom:8px}
.hero h1 .big{display:block;font-size:64px}
.hero p{position:absolute;left:76px;top:283px;color:var(--white);font-weight:700;font-size:24px}
/* intro */
.intro-head{left:60px;top:788px;width:1080px;text-align:center;color:var(--teal-text);font-size:32px;line-height:41px}
.intro-copy{left:616px;top:962px;width:520px;font-size:16.5px;line-height:30.5px}
.intro-copy h3{color:var(--blue);font-size:21px;font-weight:700;margin:18px 0 8px}
.ticks{list-style:none}
.ticks li{position:relative;padding-left:33px;margin-bottom:13px;line-height:30.5px}
.ticks li svg{position:absolute;left:0;top:9px}
/* who */
.who-band{left:0;top:1480px;width:1200px;height:575px;background:var(--gray-band)}
.who-head{left:75px;top:1536px;color:var(--blue);font-size:32px;font-weight:700;text-transform:uppercase}
.who-copy{left:75px;top:1596px;width:570px;font-size:16.5px;line-height:29.5px}
.who-copy strong{display:block;font-size:19px;color:#111;margin-bottom:8px}
.who-copy p{margin-bottom:8px}
.join{left:75px;top:1942px;width:164px;height:49px;background:var(--dark);color:var(--white);font-size:18px;display:flex;align-items:center;justify-content:center;text-transform:uppercase}
/* why */
.why-head{left:0;top:2116px;width:1200px;text-align:center;color:var(--blue);font-size:32px;font-weight:700;text-transform:uppercase}
.card{background:var(--card);text-align:center;padding:0 24px}
.card h4{color:var(--blue);font-size:22px;font-weight:700;margin:12px 0 6px}
.card p{font-size:16.5px;line-height:26px}
.card.featured{background:linear-gradient(180deg,#1256c9 0%,#0d3d8a 50%,#0a1a33 100%);color:var(--white)}
.card.featured h4{color:var(--white)}
.shadow{left:400px;top:2480px;width:400px;height:22px;border-radius:50%;background:radial-gradient(ellipse,rgba(0,0,0,.45),rgba(0,0,0,0) 70%)}
/* footer */
.footer{left:0;top:2579px;width:1200px;height:280px;background:var(--footer);color:var(--white)}
.footer h5{position:absolute;font-size:17px;font-weight:700;text-transform:uppercase}
.footer .col{position:absolute;font-size:14px;line-height:32.5px}
.footer .brand-foot{position:absolute;left:75px;top:60px;font-weight:900;font-size:24px}
.footer .copy{position:absolute;left:75px;top:172px;font-size:12.5px;line-height:22px}
</style>
</head>
<body>

<nav class="topnav abs">
  <a class="active" href="#" style="left:75px">Home</a>
  <a href="#" style="left:186px">About Us</a>
  <a href="#" style="left:323px">Services Offered</a>
  <a href="#" style="left:530px">Pricing</a>
  <a href="#" style="left:648px">Testimonials</a>
  <a href="#" style="left:820px">FAQs</a>
  <a href="#" style="left:910px">Blog</a>
  <a href="#" style="left:1003px">Contact Us</a>
</nav>

<div class="phone abs">
  <svg width="52" height="52" viewBox="0 0 52 52"><circle cx="26" cy="26" r="23" fill="none" stroke="#1a66d6" stroke-width="3" stroke-dasharray="110 35"/><path d="M19 17c2-2 4 0 5 2s-1 3-1 4 3 5 5 6 2-1 4-1 4 3 2 5c-3 3-8 1-12-3s-6-10-3-13z" fill="#1a66d6"/></svg>
  <span>1-800-555-0142</span>
</div>
<div class="brand abs">RemoteHaven</div>
<a class="btn abs" href="#" style="left:845px;top:92px;width:282px;height:44px">Request Virtual Assistance</a>

<section class="hero abs" role="img" aria-label="Businessman touching a glowing network of connected people icons">
  <h1><span class="small">Welcome to</span><span class="big">RemoteHaven</span></h1>
  <p>We are a virtual employee recruitment agency.</p>
  <a class="btn" href="#" style="position:absolute;left:75px;top:343px;width:282px;height:43px">Request Virtual Assistance</a>
</section>

<h2 class="intro-head abs">Tired of being stuck in your 9-5 cubicle job? Exhausted from commuting to and from the office? Want to spend more time with your family? We’ve got you covered.</h2>

<svg class="abs" style="left:100px;top:940px" width="480" height="475" viewBox="0 0 480 475">
  <defs><radialGradient id="g1" cx="50%" cy="55%" r="60%"><stop offset="0" stop-color="#3a7ad0"/><stop offset="1" stop-color="#0c2f6b"/></radialGradient></defs>
  <circle cx="239" cy="237" r="236" fill="#262626"/>
  <path d="M239 5 A232 232 0 0 0 239 469 A220 220 0 0 1 239 5z" fill="#1a5fd0"/>
  <circle cx="245" cy="233" r="214" fill="url(#g1)" role="img" aria-label="Hand aiming a dart at a target surrounded by people icons"/>
</svg>

<div class="intro-copy abs">
  <p>RemoteHaven is a virtual staffing company that helps freelancers and virtual assistants find their perfect work-from-home job. We have a pool of clients from all over the world who are all looking for talented virtual assistants.</p>
  <h3>With RemoteHaven, you get to:</h3>
  <ul class="ticks">
    <li><svg width="15" height="15" viewBox="0 0 15 15"><circle cx="7.5" cy="7.5" r="7.5" fill="#1a66d6"/><path d="M4 7.7l2.4 2.3L11 5.3" stroke="#fff" stroke-width="2" fill="none"/></svg>Work from the comfort of your home</li>
    <li><svg width="15" height="15" viewBox="0 0 15 15"><circle cx="7.5" cy="7.5" r="7.5" fill="#1a66d6"/><path d="M4 7.7l2.4 2.3L11 5.3" stroke="#fff" stroke-width="2" fill="none"/></svg>Have a competitive and steady income</li>
    <li><svg width="15" height="15" viewBox="0 0 15 15"><circle cx="7.5" cy="7.5" r="7.5" fill="#1a66d6"/><path d="M4 7.7l2.4 2.3L11 5.3" stroke="#fff" stroke-width="2" fill="none"/></svg>Achieve work-life balance</li>
    <li><svg width="15" height="15" viewBox="0 0 15 15"><circle cx="7.5" cy="7.5" r="7.5" fill="#1a66d6"/><path d="M4 7.7l2.4 2.3L11 5.3" stroke="#fff" stroke-width="2" fill="none"/></svg>Learn new skills for free</li>
    <li><svg width="15" height="15" viewBox="0 0 15 15"><circle cx="7.5" cy="7.5" r="7.5" fill="#1a66d6"/><path d="M4 7.7l2.4 2.3L11 5.3" stroke="#fff" stroke-width="2" fill="none"/></svg>Work with a dedicated team who can provide you with HR, payroll, IT, and training assistance 24/7!</li>
  </ul>
</div>

<div class="who-band abs"></div>
<h2 class="who-head abs">Who are our virtual assistants?</h2>
<div class="who-copy abs">
  <strong>We have VAs from all over the Philippines.</strong>
  <p>Our VA pool is composed of highly dedicated people armed with the right set of skills clients are looking for in a virtual assistant. We hire VAs of varying work experience and skill levels, and we help our VAs improve their skills so that they can get the jobs and clients they want.</p>
  <p>RemoteHaven accepts VAs in a variety of niches. Currently, our VAs belongs to one or more of the following groups: Administrative VAs, eCommerce VAs, and Specialist VAs.</p>
  <p>Are you ready to join the team? To start the application process, please click on the button below.</p>
</div>
<a class="join abs" href="#">Join Now</a>

<svg class="abs" style="left:652px;top:1530px" width="478" height="475" viewBox="0 0 478 475">
  <defs><linearGradient id="g2" x1="0" y1="0" x2="1" y2="1"><stop offset="0" stop-color="#8a6a55"/><stop offset=".5" stop-color="#d9d6d2"/><stop offset="1" stop-color="#ecebea"/></linearGradient></defs>
  <circle cx="237" cy="237" r="236" fill="#262626"/>
  <path d="M237 22 A215 215 0 0 1 237 468 A228 228 0 0 0 237 22z" fill="#1a5fd0"/>
  <circle cx="232" cy="242" r="212" fill="url(#g2)" role="img" aria-label="Smiling woman on a video call shown on a laptop screen"/>
</svg>

<h2 class="why-head abs">Why work for RemoteHaven?</h2>
<svg class="abs" style="left:46px;top:2328px" width="14" height="24" viewBox="0 0 14 24"><path d="M12 2L3 12l9 10" stroke="#222" stroke-width="3" fill="none"/></svg>
<svg class="abs" style="left:1141px;top:2328px" width="14" height="24" viewBox="0 0 14 24"><path d="M2 2l9 10-9 10" stroke="#222" stroke-width="3" fill="none"/></svg>

<div class="card abs" style="left:75px;top:2210px;width:330px;height:257px;padding-top:27px">
  <svg width="62" height="72" viewBox="0 0 62 72"><circle cx="31" cy="40" r="27" fill="none" stroke="#222" stroke-width="2.5"/><circle cx="31" cy="40" r="16" fill="none" stroke="#222" stroke-width="2"/><rect x="25" y="3" width="12" height="7" fill="none" stroke="#222" stroke-width="2"/><path d="M31 10v3M35 33c-2-2-8-2-8 1s8 2 8 6-6 3-8 1M31 29v22" stroke="#222" stroke-width="2" fill="none"/></svg>
  <h4>Competitive Hourly Rates</h4>
  <p>We offer competitive rates based on your years of experience and skill proficiency.</p>
</div>
<div class="card featured abs" style="left:436px;top:2192px;width:330px;height:292px;padding-top:45px">
  <svg width="66" height="66" viewBox="0 0 66 66"><rect x="2" y="6" width="50" height="44" fill="none" stroke="#fff" stroke-width="2.5"/><path d="M2 16h50M9 2v8M17 2v8M25 2v8M33 2v8M41 2v8M10 26h10l12 12h10M10 38h10l12-12h10" stroke="#fff" stroke-width="2" fill="none"/><circle cx="52" cy="52" r="12" fill="#0d3d8a" stroke="#fff" stroke-width="2.5"/><path d="M52 45v7l4 3" stroke="#fff" stroke-width="2" fill="none"/></svg>
  <h4>Flexible Hours</h4>
  <p>Full-time or part-time? We’ll match you with a client whose staffing needs perfectly matches your availability!</p>
</div>
<div class="shadow abs"></div>
<div class="card abs" style="left:797px;top:2210px;width:330px;height:257px;padding-top:27px">
  <svg width="68" height="70" viewBox="0 0 68 70"><rect x="2" y="6" width="64" height="62" fill="none" stroke="#222" stroke-width="2.5"/><path d="M2 18h64M10 2v8M18 2v8M26 2v8M34 2v8M42 2v8M50 2v8M58 2v8M14 30h40M14 44h40M14 58h40" stroke="#222" stroke-width="2" fill="none"/><rect x="26" y="25" width="14" height="10" fill="none" stroke="#222" stroke-width="2"/><rect x="20" y="39" width="14" height="10" fill="none" stroke="#222" stroke-width="2"/><rect x="34" y="53" width="14" height="10" fill="none" stroke="#222" stroke-width="2"/></svg>
  <h4>Flexible Schedule</h4>
  <p>We have clients from different time zones all over the world. We’ll help you find the best fit.</p>
</div>

<footer class="footer abs">
  <div class="brand-foot">RemoteHaven</div>
  <div class="copy">Copyright© 2020 Company Name<br>All Right Reserved.</div>
  <h5 style="left:342px;top:55px">Site Map</h5>
  <div class="col" style="left:342px;top:85px">Home<br>About Us<br>Services offered<br>Pricing</div>
  <div class="col" style="left:488px;top:85px">Testimonials<br>FAQs<br>Blog<br>Contact Us</div>
  <h5 style="left:676px;top:55px">Services</h5>
  <div class="col" style="left:676px;top:85px">Cras sit amet<br>Enim orci<br>Mauris vitae porttitor<br>Nullam viverra</div>
  <h5 style="left:914px;top:55px">Contact Info</h5>
  <div class="col" style="left:914px;top:88px;font-size:13.5px;line-height:23px">42 Fenwick Lane<br>Harbourton, HB2 7QX</div>
  <div class="col" style="left:914px;top:133px;line-height:28px">
    <svg width="12" height="12" viewBox="0 0 12 12"><path d="M2 1c1-1 2 0 3 1s-1 2 0 3 2 2 3 1 2 0 3 1-1 4-4 2-6-6-5-8z" fill="#fff"/></svg><span style="margin-left:20px">1-800-555-0178</span><br>
    <svg width="13" height="10" viewBox="0 0 13 10"><rect width="13" height="10" fill="#fff"/><path d="M0 0l6.5 5L13 0" stroke="#2a2a2a" stroke-width="1.5" fill="none"/></svg><span style="margin-left:19px">info@remotehaven.example</span>
  </div>
</footer>

</body>
</html>
```